I need a business card design for a new business based in South West Australia.
I specialize in residential window cleaning & general handyman maintenance.

Dale Marsh - 412 SILVER HAWK DETAILING
- Window Cleaning
- House Maintenance

```html
<!DOCTYPE html>
<html lang="en">
<head>
<meta charset="UTF-8">
<title>412 Silver Hawk Detailing – Business Card</title>
<link rel="stylesheet" href="https://fonts.googleapis.com/css2?family=Open+Sans:wght@400;600;800&display=swap">
<style>
  :root {
    --backdrop: #3a3330;
    --card: #141414;
    --card-edge: #1f1f1f;
    --blue: #2f79d6;
    --orange: #f07a1a;
    --silver: #8a8a8a;
  }
  * { box-sizing: border-box; margin: 0; padding: 0; }
  html, body {
    width: 1200px; height: 900px; overflow: hidden;
    background: var(--backdrop);
    font-family: "Open Sans", sans-serif;
  }
  .stage {
    position: relative; width: 1200px; height: 900px;
    display: flex; align-items: center; justify-content: center; gap: 50px;
  }
  .card {
    width: 525px; height: 300px;
    background: var(--card);
    border: 1px solid var(--card-edge);
    position: relative;
    overflow: hidden;
  }
  .card--front { display: flex; }
  .brand {
    width: 300px; flex: none;
    display: flex; flex-direction: column;
    justify-content: flex-end; align-items: center;
    padding: 0 12px 78px 16px;
  }
  .brand__name {
    color: var(--blue); font-weight: 800; font-size: 18px;
    letter-spacing: 0; white-space: nowrap;
  }
  .brand__tagline {
    color: var(--orange); font-weight: 800; font-size: 8.5px;
    letter-spacing: 0.5px; margin-top: 3px; white-space: nowrap;
  }
  .divider {
    width: 1px; flex: none; margin: 60px 0 70px;
    background: linear-gradient(to bottom, transparent, var(--orange), transparent);
  }
  .contact { padding: 52px 0 0 22px; min-width: 0; }
  .contact__name { color: var(--orange); font-weight: 600; font-size: 15px; }
  .contact__role { color: var(--blue); font-size: 12px; margin-bottom: 16px; }
  .contact__address { color: var(--blue); font-size: 12px; line-height: 1.35; margin-bottom: 14px; }
  .contact__line {
    color: var(--blue); font-size: 12px; line-height: 1.55;
    display: flex; align-items: center; gap: 7px;
  }
  .contact__line svg { width: 10px; height: 10px; fill: var(--orange); flex: none; }
  .card--back { display: flex; align-items: center; justify-content: center; }
  .back__name {
    color: var(--silver); font-weight: 800; font-size: 24px; letter-spacing: 0.5px;
    white-space: nowrap;
  }
</style>
</head>
<body>
<main class="stage">
  <section class="card card--front" aria-label="Card front">
    <div class="brand">
      <div class="brand__name">412 SILVER HAWK DETAILING</div>
      <div class="brand__tagline">WINDOW CLEANING &amp; HOUSE MAINTENANCE</div>
    </div>
    <div class="divider"></div>
    <div class="contact">
      <p class="contact__name">Dale Marsh</p>
      <p class="contact__role">Managing Director</p>
      <p class="contact__address">12345, Address Goes Here<br>Country Name, 123456.</p>
      <p class="contact__line">
        <svg viewBox="0 0 10 10" aria-hidden="true"><path d="M1 3c0-1 1-2 4-2s4 1 4 2v1H7V3H3v1H1zM2 5h6l1 4H1z"/></svg>
        044-123 456 789
      </p>
      <p class="contact__line">
        <svg viewBox="0 0 10 10" aria-hidden="true"><path d="M0 2h10v6H0zM1 3v.3l4 2.7 4-2.7V3z"/></svg>
        info@webname.com
      </p>
    </div>
  </section>
  <section class="card card--back" aria-label="Card back">
    <div class="back__name">412 SILVER HAWK DETAILING</div>
  </section>
</main>
</body>
</html>
```